Zimbal, a future commerce website

Zimbal will be a commerce website; the project is quite large, and for now I just require three pages and the main bar to be crafted; If chosen your design, I will require you to work with me in a freelance job for the rest of the site to be made.
The following is one way to put Zimbal’s building blocks; you can propose another.
A list of webpages, whose design I like, is in the first document.
-Design specification
Zimbal’s interface should be minimal and intuitive.
Its design should make the user perceive Zimbal as innovative; I will incline for an out of the box design.
--Main bar
It will contain the site logo, a search bar, and four buttons, listed below.
---Notifications button
It will display a sidebar with containers; each container will have an icon, the notification, and one or two buttons; two example notifications and its respective buttons are in the second document.
It shall stand out when there are unseen notifications.
---Shopping cart button
A sidebar will be toggled on click with added product previews.
---Sell Button
---Account button
When clicked it will display a pane whose elements will depend on the user
status.
----If logged
It will display seller’s store image, a button linking to the main section of the account section, a button linking to in-process bought items of the account section, and a button linking to in-process sold items of the account section.
----If not logged
It will contain the elements for the user to either log in or register; for the former, email or username and password will be asked, for the latter, username, email, and password, this last one being asked twice.
--Product previews
Each, will have a title, a product image, and the product’s most important characteristics; most characteristics will have alongside an icon, which will display on mouse over the characteristic name, or, a name. Characteristics of two product categories whose product previews will contain an icon alongside are in the third document.
--Main page
Product previews of several categories will be displayed here; in order to reflect recommendation, some should have distinct size.
A list of categories will be present in this page; it may be toggled by a button contained in the main bar, or be displayed permanently.
A text conveying the message that all purchases made with Zimbal payment system are protected will be contained in a full width element which will be positioned below the main bar of this page; a “Learn more” link will be positioned in this element.
--Product page creation page
It will be displayed as part of the publication page.
It will be a "what you see is what you get" design system; the user will choose from several templates and fill the appropriate spaces; where text must be put, sample text will be present, and, where an image must, a plus sign and a “Add image” text will be present; submit please two templates; for the user to be able to add more content, at the bottom of the template there will be four layouts, upon click of one, it will be added.
Regarding the shipping menu, there will always be an empty box with a plus sign and a “Add shipping option” text, if clicked the user will be able to either fill it with company name, shipping time, and price, or to put the text “Arrange with seller” in it (if there is no other box with that text).
--Product page
It will not occupy the whole viewport; there will be vertical holes at the leftmost and rightmost parts of the viewport.
It will contain: price (which should include shipping in type one publications), sale price (for some product pages), countdown of sale price, average seller’s handling time, seller’s reputation indicator as measured by percentage of positive reviews received, seller’s store/profile image, seller’s username, a shipping menu consisting of boxes (selected will be displayed differently), “Buy” and “Add to cart” buttons, a section to view and ask questions, and seller provided images and text.
Previews of similar products will also be present.
Reason: Designs still require some work

```html
<!DOCTYPE html>
<html lang="en">
<head>
<meta charset="utf-8">
<title>Zimbal – Home</title>
<link rel="stylesheet" href="https://fonts.googleapis.com/css2?family=Open+Sans:wght@300;400;600;700&display=swap">
<style>
:root{
  --red:#e64a4d;
  --red-dark:#c93a3e;
  --ink:#333333;
  --muted:#8a8a8a;
  --line:#e2e2e2;
  --band:#efefef;
  --footer:#f3f3f3;
  --white:#ffffff;
}
*{box-sizing:border-box;margin:0;padding:0}
html,body{width:705px;height:1200px;overflow:hidden;background:var(--white)}
body{position:relative;font-family:'Open Sans',Arial,sans-serif;color:var(--ink)}
.abs{position:absolute}

/* top strip */
.top-strip{left:0;top:0;width:705px;height:16px;background:var(--red-dark);color:var(--white);font-size:6px;display:flex;align-items:center;padding:0 18px;justify-content:space-between}
.top-strip .contact{display:flex;align-items:center;gap:4px}
.top-strip .right{display:flex;align-items:center;gap:5px}
.top-strip .dot{width:7px;height:7px;border-radius:50%;background:rgba(255,255,255,.85)}
.top-strip .account{margin-left:8px;font-weight:600}

/* header */
.header{left:0;top:16px;width:705px;height:78px}
.logo{left:20px;top:28px;display:flex;align-items:center;gap:6px}
.logo .mark{width:16px;height:16px;background:var(--red)}
.logo .name{font-size:20px;font-weight:700;color:var(--red);letter-spacing:.5px}
.search{left:223px;top:32px;width:330px;height:18px;border:1px solid var(--line);display:flex;align-items:center;justify-content:space-between;padding:0 6px;font-size:6px;color:var(--muted)}
.tools{left:566px;top:34px;display:flex;gap:6px}
.tools .tool{width:14px;height:14px;border-radius:50%;background:#555;display:flex;align-items:center;justify-content:center}

/* benefits */
.benefits{left:0;top:94px;width:705px;height:82px;background:var(--band)}
.benefits h2{position:absolute;top:7px;width:100%;text-align:center;font-size:11px;font-weight:600;color:var(--red);letter-spacing:.5px}
.benefit{position:absolute;top:42px;display:flex;gap:6px;align-items:flex-start}
.benefit h3{font-size:6px;font-weight:700;text-transform:uppercase}
.benefit p{font-size:5.5px;color:var(--muted);margin-top:2px}

/* nav */
.main-nav{left:0;top:176px;width:705px;height:29px;background:var(--red);display:flex;align-items:center;padding-left:23px;gap:26px;color:var(--white);font-size:6.5px;font-weight:600;text-transform:uppercase}

/* hero */
.hero{left:0;top:205px;width:705px;height:305px;background:linear-gradient(90deg,#efe2cf 0%,#e7d3b8 45%,#f3ead9 100%)}
.hero-copy{left:470px;top:300px;width:210px}
.hero-copy .kicker{font-size:24px;font-weight:300;color:var(--red);text-align:right;line-height:1}
.hero-copy .title{font-size:30px;font-weight:400;color:var(--red);text-align:right;line-height:1.15}
.hero-copy p{font-size:7px;color:#555;text-align:right;margin-top:6px;line-height:1.5}
.btn{background:var(--red);color:var(--white);font-size:6.5px;font-weight:700;text-transform:uppercase;display:flex;align-items:center;justify-content:center}
.hero-btn{left:545px;top:402px;width:72px;height:20px}
.hero-dots{left:336px;top:490px;display:flex;gap:4px}
.hero-dots span{width:5px;height:5px;border-radius:50%;background:rgba(255,255,255,.7)}
.hero-dots span.on{background:var(--white);box-shadow:0 0 0 1px #ccc}

/* best sellers */
.section-title{left:56px;top:537px;font-size:12px;font-weight:700;letter-spacing:.3px}
.arrows{left:468px;top:538px;display:flex;gap:4px}
.arrows span{width:12px;height:12px;border-radius:50%;border:1px solid #bbb;display:flex;align-items:center;justify-content:center}
.product{position:absolute;width:140px;border:1px solid var(--line);background:var(--white)}
.product .photo{width:100%;height:112px}
.product .caption{height:24px;display:flex;align-items:center;justify-content:center;font-size:5.5px;color:var(--muted)}
.product.active .caption{background:var(--red);color:var(--white)}

/* new arrivals */
.aside-head{left:522px;top:530px;width:125px;height:20px;background:var(--red);color:var(--white);font-size:7px;font-weight:700;display:flex;align-items:center;padding-left:7px;text-transform:uppercase}
.arrival{left:522px;top:550px;width:125px;height:225px;border:1px solid var(--line)}
.arrival .photo{position:absolute;left:15px;top:14px;width:95px;height:90px}
.stars{position:absolute;left:10px;top:116px;display:flex;gap:1px;align-items:center;font-size:5px;color:var(--muted)}
.arrival h4{position:absolute;left:10px;top:128px;font-size:7px;font-weight:600}
.arrival p{position:absolute;left:10px;top:142px;width:105px;font-size:5.5px;color:var(--muted);line-height:1.5}
.arrival .more{position:absolute;left:10px;top:176px;font-size:5.5px;color:var(--red);font-weight:600}
.promo{left:522px;top:800px;width:125px;height:175px;background:#f2f2f2}
.promo .photo{position:absolute;right:0;top:0;width:75px;height:175px}
.promo h4{position:absolute;left:8px;top:40px;width:60px;font-size:10px;font-weight:700;line-height:1.2}
.promo a{position:absolute;left:8px;top:88px;font-size:8px;color:var(--red);text-decoration:underline;font-weight:600}

/* protection notice */
.notice{left:56px;top:884px;width:450px;text-align:center;font-size:8px;line-height:1.55;color:#555}
.notice-btn{left:246px;top:946px;width:70px;height:19px}

/* footer */
.footer{left:0;top:1000px;width:705px;height:185px;background:var(--footer)}
.f-col{position:absolute;top:18px}
.f-col h5{font-size:6.5px;font-weight:700;color:var(--red);text-transform:uppercase;margin-bottom:6px}
.f-col h6{font-size:10px;font-weight:400;color:#555;margin-bottom:8px}
.f-col li{list-style:none;font-size:6px;color:#555;line-height:1.9}
.f-col p{font-size:5.5px;color:var(--muted);line-height:1.5}
.field{width:100px;height:15px;border:1px solid var(--line);background:var(--white);font-size:5.5px;color:var(--muted);display:flex;align-items:center;padding-left:5px;margin-top:6px}
.signup{display:flex;gap:4px;align-items:flex-end}
.signup .btn{width:32px;height:15px}
.story{display:flex;gap:6px;align-items:center;margin-top:8px}
.avatar{width:16px;height:16px;border-radius:50%;background:#c9b49d}
.social li{display:flex;align-items:center;gap:5px}
.social li span{width:6px;height:6px;border-radius:50%;background:var(--red)}
.copyright{left:0;top:1185px;width:705px;height:15px;display:flex;align-items:center;justify-content:center;font-size:5px;color:var(--muted)}
</style>
</head>
<body>

<div class="abs top-strip">
  <div class="contact">
    <svg width="7" height="5" viewBox="0 0 7 5"><rect x=".5" y=".5" width="6" height="4" fill="none" stroke="#fff" stroke-width=".8"/><path d="M.5 .5 3.5 3 6.5 .5" fill="none" stroke="#fff" stroke-width=".8"/></svg>
    <span>hello@zimbal.com</span>
  </div>
  <div class="right">
    <span class="dot"></span><span class="dot"></span><span class="dot"></span><span class="dot"></span><span class="dot"></span>
    <span class="account">MY ACCOUNT ▾</span>
  </div>
</div>

<header class="abs header">
  <div class="abs logo"><span class="mark"></span><span class="name">ZIMBAL</span></div>
  <div class="abs search">
    <span>Search Here</span>
    <svg width="8" height="8" viewBox="0 0 8 8"><circle cx="3.3" cy="3.3" r="2.4" fill="none" stroke="#555" stroke-width="1"/><path d="M5 5 7.3 7.3" stroke="#555" stroke-width="1.1"/></svg>
  </div>
  <div class="abs tools">
    <span class="tool"><svg width="8" height="8" viewBox="0 0 8 8"><path d="M2 6V3.5a2 2 0 0 1 4 0V6H2ZM3.3 7h1.4" fill="#fff" stroke="#fff" stroke-width=".6"/></svg></span>
    <span class="tool"><svg width="8" height="8" viewBox="0 0 8 8"><path d="M1 1.5h1.2l.9 3.8h3.3l.7-2.6H2.6" fill="none" stroke="#fff" stroke-width=".8"/><circle cx="3.4" cy="6.6" r=".6" fill="#fff"/><circle cx="6" cy="6.6" r=".6" fill="#fff"/></svg></span>
    <span class="tool"><svg width="8" height="8" viewBox="0 0 8 8"><path d="M4 1.5v5M1.5 4h5" stroke="#fff" stroke-width="1.1"/></svg></span>
    <span class="tool"><svg width="8" height="8" viewBox="0 0 8 8"><circle cx="4" cy="2.8" r="1.5" fill="#fff"/><path d="M1.3 7.2a2.7 2.7 0 0 1 5.4 0Z" fill="#fff"/></svg></span>
  </div>
</header>

<section class="abs benefits">
  <h2>BENEFITS</h2>
  <div class="benefit" style="left:70px">
    <svg width="12" height="13" viewBox="0 0 12 13"><path d="M6 1 11 3v4c0 3-2.5 4.5-5 5.5C3.5 11.5 1 10 1 7V3Z" fill="#777"/></svg>
    <div><h3>Protected Payment</h3><p>Lorem ipsum dolor amet consectetur</p></div>
  </div>
  <div class="benefit" style="left:272px">
    <svg width="13" height="12" viewBox="0 0 13 12"><path d="M2 4h8l-2-2M11 8H3l2 2" fill="none" stroke="#777" stroke-width="1.4"/></svg>
    <div><h3>14 Days Free Returns</h3><p>Lorem ipsum dolor amet consectetur</p></div>
  </div>
  <div class="benefit" style="left:470px">
    <svg width="14" height="11" viewBox="0 0 14 11"><rect x="1" y="1" width="12" height="9" rx="1" fill="#777"/><rect x="1" y="3" width="12" height="1.6" fill="#efefef"/></svg>
    <div><h3>Cash on Delivery</h3><p>Lorem ipsum dolor amet consectetur</p></div>
  </div>
</section>

<nav class="abs main-nav">
  <span>Home</span><span>About Us</span><span>Fashion Accessories</span><span>Women Style</span><span>Men's Style</span><span>Contact Us</span>
</nav>

<section class="abs hero" role="img" aria-label="Fashion photo: woman in a polka-dot dress holding a red handbag"></section>
<div class="abs hero-copy">
  <div class="kicker">Sell Fashion</div>
  <div class="title">ACCESSORIES</div>
  <p>Lorem ipsum dolor sit amet, consectetur adipiscing elit, sed do eiusmod tempor incididunt ut labore et dolore.</p>
</div>
<div class="abs btn hero-btn">Shop Now</div>
<div class="abs hero-dots"><span class="on"></span><span></span><span></span><span></span></div>

<h2 class="abs section-title">BEST SELLERS</h2>
<div class="abs arrows">
  <span><svg width="5" height="5" viewBox="0 0 5 5"><path d="M3.5 .5 1.5 2.5 3.5 4.5" fill="none" stroke="#888"/></svg></span>
  <span><svg width="5" height="5" viewBox="0 0 5 5"><path d="M1.5 .5 3.5 2.5 1.5 4.5" fill="none" stroke="#888"/></svg></span>
</div>

<div class="product active" style="left:56px;top:565px">
  <div class="photo" role="img" aria-label="Product photo: leather handbag" style="background:linear-gradient(160deg,#ece6dc,#a8835a)"></div>
  <div class="caption">Phasellus sed nisi comfort</div>
</div>
<div class="product" style="left:211px;top:565px">
  <div class="photo" role="img" aria-label="Product photo: wedge sandals" style="background:linear-gradient(160deg,#f4f1ec,#c08a55)"></div>
  <div class="caption">Phasellus sed nisi comfort</div>
</div>
<div class="product" style="left:366px;top:565px">
  <div class="photo" role="img" aria-label="Product photo: gift box with accessories" style="background:linear-gradient(160deg,#f5f5f5,#b9bcc0)"></div>
  <div class="caption">Phasellus sed nisi comfort</div>
</div>
<div class="product" style="left:56px;top:722px">
  <div class="photo" role="img" aria-label="Product photo: desktop monitor" style="background:linear-gradient(160deg,#2f6fb8,#1b3e6e)"></div>
  <div class="caption">Phasellus sed nisi comfort</div>
</div>
<div class="product" style="left:211px;top:722px">
  <div class="photo" role="img" aria-label="Product photo: tablet held by the sea" style="background:linear-gradient(160deg,#9cc3db,#3d5a6e)"></div>
  <div class="caption">Phasellus sed nisi comfort</div>
</div>
<div class="product" style="left:366px;top:722px">
  <div class="photo" role="img" aria-label="Product photo: camera in hand" style="background:linear-gradient(160deg,#6a6a6a,#1e1e1e)"></div>
  <div class="caption">Phasellus sed nisi comfort</div>
</div>

<div class="abs aside-head">New Arrivals</div>
<div class="abs arrival">
  <div class="photo" role="img" aria-label="Product photo: silver ring" style="background:radial-gradient(circle,#ffffff 30%,#d4d4d4 100%)"></div>
  <div class="stars">
    <svg width="30" height="6" viewBox="0 0 30 6"><g fill="#f0b323"><path d="M3 0 3.8 2H6L4.2 3.3 4.9 5.6 3 4.2 1.1 5.6 1.8 3.3 0 2H2.2Z"/><path transform="translate(6)" d="M3 0 3.8 2H6L4.2 3.3 4.9 5.6 3 4.2 1.1 5.6 1.8 3.3 0 2H2.2Z"/><path transform="translate(12)" d="M3 0 3.8 2H6L4.2 3.3 4.9 5.6 3 4.2 1.1 5.6 1.8 3.3 0 2H2.2Z"/><path transform="translate(18)" d="M3 0 3.8 2H6L4.2 3.3 4.9 5.6 3 4.2 1.1 5.6 1.8 3.3 0 2H2.2Z"/></g><path transform="translate(24)" d="M3 0 3.8 2H6L4.2 3.3 4.9 5.6 3 4.2 1.1 5.6 1.8 3.3 0 2H2.2Z" fill="#ccc"/></svg>
    <span>1 Review</span>
  </div>
  <h4>Duis aute irure dolor in</h4>
  <p>Lorem ipsum dolor sit amet, consectetur adipiscing elit sed do eiusmod.</p>
  <span class="more">View Details</span>
</div>

<div class="abs promo">
  <div class="photo" role="img" aria-label="Photo: smiling man in a yellow shirt" style="background:linear-gradient(180deg,#f3f3f3 0%,#e9cf5a 55%,#e2bf2e 100%)"></div>
  <h4>New Essentials Collection</h4>
  <a>Shop Now</a>
</div>

<p class="abs notice">all purchases made with Zimbal payment system are<br>protected will be contained in a full width element which will be positioned<br>below the main bar of this page</p>
<div class="abs btn notice-btn" style="text-transform:none;font-weight:600">Learn More</div>

<footer class="abs footer">
  <div class="f-col" style="left:56px">
    <h5>My Account</h5>
    <ul><li>Shipping &amp; Returns</li><li>About Us</li><li>Terms &amp; Conditions</li><li>Contact Us</li><li>Blog</li><li>Privacy</li></ul>
  </div>
  <div class="f-col" style="left:205px;width:140px">
    <h6>Newsletter Sign up</h6>
    <p>Excepteur sint occaecat cupidatat non proident, sunt in culpa qui.</p>
    <div class="field">Enter your Name</div>
    <div class="signup"><div class="field">Enter your Email</div><div class="btn" style="text-transform:none">Sign Up</div></div>
  </div>
  <div class="f-col" style="left:390px;width:140px">
    <h6>Client Stories</h6>
    <p>Lorem ipsum dolor sit amet, consectetur adipiscing elit, sed do eiusmod tempor incididunt.</p>
    <div class="story"><span class="avatar" role="img" aria-label="Client portrait"></span><p>Alex Moor - Manager</p></div>
  </div>
  <div class="f-col social" style="left:585px">
    <h5 style="color:#555">Social Media</h5>
    <ul><li><span></span>Friendwall</li><li><span></span>Chirper</li><li><span></span>Snapgram</li><li><span></span>Pinboard</li></ul>
  </div>
</footer>
<div class="abs copyright">© 2016 ZIMBAL - ALL RIGHTS RESERVED. TERMS AND CONDITIONS</div>

</body>
</html>
```